Prime Global Casting Agency Needs creative business card design

We manage actors careers and book them liaising and promoting their profiles internationally through Casting Directors, Producers, Directors, Publicists etc. We need clearly visable contact details but with a design that reflects our status and creativity of TV, Feature Film industry. Our logo is attached and needs to relate and our website is www.brisklanestagefolk.com
No flame designs please but please incorporate logo colours.

Target Market(s)

Clients

Industry/Entity Type

Film Production

Contact Information for Business Card

Director Danielle Prowse
Suite F, Building 4, Wrenlow Studios Australia, Kelby Vale, Sydney, NSW 2048

Font styles to use
Sans Serif

Colors
ec1f27

Requirements
Nice to have
• Colours should relate to logo attached and type can relate again to type in the logo design.
Should not have
• No Flames designs and best to be not too obvious with the film designs eiither. Needs to be more creative and modern

```html
<!DOCTYPE html>
<html lang="en">
<head>
<meta charset="utf-8">
<title>Brisklane Stagefolk – Business Card</title>
<link rel="stylesheet" href="https://fonts.googleapis.com/css2?family=PT+Sans:wght@400;700&display=swap">
<style>
  :root {
    --brand-red: #ec1f27;
    --deep-red: #b3141c;
    --paper: #ffffff;
    --ink: #3a3a3a;
    --backdrop: #e9e6e2;
  }
  * { margin: 0; padding: 0; box-sizing: border-box; }
  html, body { width: 1200px; height: 1200px; overflow: hidden; }
  body {
    background: var(--backdrop);
    font-family: "PT Sans", Arial, sans-serif;
    display: flex;
    flex-direction: column;
    align-items: center;
    justify-content: center;
    gap: 40px;
  }
  .card {
    position: relative;
    width: 960px;
    height: 540px;
    overflow: hidden;
    box-shadow: 0 6px 18px rgba(0,0,0,0.18);
  }
  .card-front {
    background: var(--brand-red);
    display: flex;
    align-items: center;
    justify-content: center;
  }
  .brand-name {
    font-weight: 700;
    letter-spacing: 1px;
    white-space: nowrap;
  }
  .card-front .brand-name { color: var(--paper); font-size: 72px; }
  .card-back { background: var(--paper); }
  .card-back .bands { position: absolute; inset: 0; }
  .holder {
    position: absolute;
    left: 0;
    top: 36px;
    display: flex;
    align-items: flex-start;
    gap: 14px;
  }
  .holder-name { color: var(--brand-red); font-size: 34px; font-weight: 700; line-height: 1.05; }
  .holder-title { color: var(--ink); font-size: 22px; }
  .contact {
    position: absolute;
    left: 48px;
    top: 190px;
    color: var(--ink);
    font-size: 22px;
    line-height: 1.3;
    list-style: none;
  }
  .contact .label { color: var(--brand-red); }
  .card-back .brand-name {
    position: absolute;
    left: 470px;
    top: 210px;
    color: var(--brand-red);
    font-size: 54px;
  }
</style>
</head>
<body>
  <section class="card card-front" aria-label="Card front">
    <span class="brand-name">Brisklane Stagefolk</span>
  </section>

  <section class="card card-back" aria-label="Card back">
    <svg class="bands" width="960" height="540" viewBox="0 0 960 540" aria-hidden="true">
      <polygon points="0,36 48,36 0,84" fill="var(--deep-red)"/>
      <polygon points="48,36 48,84 0,84" fill="var(--brand-red)"/>
      <polygon points="0,380 330,380 300,408 0,408" fill="var(--deep-red)"/>
      <polygon points="330,408 960,408 960,540 450,540" fill="var(--brand-red)" opacity="0"/>
      <polygon points="330,420 960,420 960,470 300,470" fill="var(--brand-red)"/>
    </svg>

    <div class="holder">
      <span style="width:48px"></span>
      <div>
        <p class="holder-name">Marcus Hale</p>
        <p class="holder-title">Managing Director</p>
      </div>
    </div>

    <ul class="contact">
      <li>Suite F, Building 4</li>
      <li>Kelby Vale, NSW 2048</li>
      <li><span class="label">p:</span> 044-555 010 482</li>
      <li><span class="label">f:</span> 044-555 010 482</li>
      <li><span class="label">e:</span> info@brisklanemail.com</li>
    </ul>

    <span class="brand-name">Brisklane Stagefolk</span>
  </section>
</body>
</html>
```